Business Card Design

We are a family run drainage & groundworks company that specialise in treatment plant installation. We work for commercial & domestic property's, we have specialised knowledge & equipment for CCTV surveys, jetting blockages & repairing all types of drainage systems.

Industry/Entity Type

Business

Contact Information for Business Card

14 Millbrook Works
Tallowen Park Lane
Harnbridge
Kestershire
SP9 4DW
Tel: 01632 960418
Fax: 01632 960773
Mobile: 07700 900382
enquiries@larkes.co.uk
www.larkfieldenvironmentalservices.co.uk

Requirements
Must have
• logo, address, the right colour green.
I need the cards to also have individuals names:

Tom marlowe
Dan Whitcombe
Emma Marlowe
Kay Dunmore

And also some with just the name & address on :)

```html
<!DOCTYPE html>
<html lang="en">
<head>
<meta charset="utf-8">
<title>Larkfield Environmental Services – Business Cards</title>
<link rel="stylesheet" href="https://fonts.googleapis.com/css2?family=Lato:wght@300;400;700;900&display=swap">
<style>
  :root {
    --backdrop: #231f20;
    --brand-green: #1aa84f;
    --paper: #ffffff;
    --ink: #231f20;
    --ink-soft: #3a3a3a;
  }
  * { margin: 0; padding: 0; box-sizing: border-box; }
  html, body {
    width: 966px;
    height: 1200px;
    overflow: hidden;
    background: var(--backdrop);
    font-family: "Lato", "Helvetica Neue", Arial, sans-serif;
  }
  .card-sheet {
    position: relative;
    width: 966px;
    height: 1200px;
  }
  .business-card {
    position: absolute;
    left: 86px;
    width: 796px;
    height: 524px;
    background: var(--paper);
    overflow: hidden;
  }
  .business-card--first { top: 56px; }
  .business-card--second { top: 613px; }

  .contact-block {
    position: absolute;
    left: 35px;
    top: 38px;
  }
  .contact-name {
    font-weight: 900;
    font-size: 29px;
    letter-spacing: 0.2px;
    color: var(--brand-green);
    text-transform: uppercase;
    line-height: 36px;
  }
  .contact-line {
    font-weight: 300;
    font-size: 25px;
    color: var(--ink-soft);
    line-height: 35px;
  }
  .contact-email {
    font-weight: 400;
    font-size: 26px;
    color: var(--ink);
    line-height: 36px;
  }

  .brand-panel {
    position: absolute;
    left: 460px;
    top: 0;
    width: 336px;
    height: 524px;
    background: var(--brand-green);
    color: var(--paper);
    text-align: center;
  }
  .brand-name {
    position: absolute;
    left: 0;
    right: 0;
    top: 140px;
    font-weight: 900;
    font-size: 62px;
    line-height: 70px;
    letter-spacing: -0.5px;
    color: var(--paper);
  }
  .brand-descriptor {
    position: absolute;
    left: 0;
    right: 0;
    top: 219px;
    font-weight: 400;
    font-size: 29px;
    line-height: 31px;
    text-transform: uppercase;
  }
  .brand-address {
    position: absolute;
    left: 0;
    right: 0;
    top: 313px;
    font-weight: 300;
    font-size: 26px;
    line-height: 35px;
    font-style: normal;
  }

  .web-band {
    position: absolute;
    left: 0;
    bottom: 0;
    width: 796px;
    height: 53px;
    background: var(--brand-green);
  }
  .web-address {
    position: absolute;
    right: 29px;
    bottom: 10px;
    font-weight: 700;
    font-size: 26px;
    line-height: 32px;
    color: var(--paper);
  }
</style>
</head>
<body>
<main class="card-sheet">

  <section class="business-card business-card--first" aria-label="Business card for Emma Marlowe">
    <div class="contact-block">
      <h2 class="contact-name">Emma Marlowe</h2>
      <p class="contact-line">tel: 01632 960418</p>
      <p class="contact-line">fax: 01632 960773</p>
      <p class="contact-line">mobile: 07700 900382</p>
      <p class="contact-email">enquiries@larkes.co.uk</p>
    </div>
    <div class="web-band"></div>
    <div class="brand-panel">
      <p class="brand-name">larkfield</p>
      <p class="brand-descriptor">Environmental<br>Services</p>
      <address class="brand-address">14 Millbrook Works<br>Tallowen Park Lane<br>Harnbridge<br>Kestershire SP9 4DW</address>
    </div>
    <p class="web-address">www.larkfieldenvironmentalservices.co.uk</p>
  </section>

  <section class="business-card business-card--second" aria-label="Business card for Tom Marlowe">
    <div class="contact-block">
      <h2 class="contact-name">Tom Marlowe</h2>
      <p class="contact-line">tel: 01632 960418</p>
      <p class="contact-line">fax: 01632 960773</p>
      <p class="contact-line">mobile: 07700 900382</p>
      <p class="contact-email">enquiries@larkes.co.uk</p>
    </div>
    <div class="web-band"></div>
    <div class="brand-panel">
      <p class="brand-name">larkfield</p>
      <p class="brand-descriptor">Environmental<br>Services</p>
      <address class="brand-address">14 Millbrook Works<br>Tallowen Park Lane<br>Harnbridge<br>Kestershire SP9 4DW</address>
    </div>
    <p class="web-address">www.larkfieldenvironmentalservices.co.uk</p>
  </section>

</main>
</body>
</html>
```